Silver Bloom Marisol's Cleaning Service Business Cards Project

A business card with all contact details with logo design on there (already have a logo) eye catching Logo and contact info on one side, full logo on the back, must target upper class residential and corporate companies, fitness companies, still keep it on the feminine side of things , must look elegant

Target Market(s)

Upper class homes and corporate companies

Industry/Entity Type

Cleaning Service

Contact Information for Business Card

Name: Marisol Quenby
Position: Director
ABN: 31647209853
Email: marisolssilvercleaning@tidymail.example
Number: 0417906354

Font styles to use
Decorative

Colors

Designer to choose colors to be used in the design.

Requirements
Must have
• Available Sydney Wide, contact info and logo on one side, full logo on the back
Nice to have
• Professional appearance
Should not have
• Cheap advert looking stuff

```html
<!DOCTYPE html>
<html lang="en">
<head>
<meta charset="utf-8">
<title>Silver Bloom – Business Cards</title>
<link rel="stylesheet" href="https://fonts.googleapis.com/css2?family=Noto+Serif:wght@400;700&family=Roboto:wght@400;500&display=swap">
<style>
  :root {
    --bg: #eeeeef;
    --card-white: #ffffff;
    --card-slate: #3b3f4a;
    --teal: #5fbcbb;
    --ink: #2f323a;
    --muted: #5a5d64;
    --rule: #b9bbbf;
  }
  * { margin: 0; padding: 0; box-sizing: border-box; }
  html, body { width: 1200px; height: 1103px; overflow: hidden; }
  body {
    background: var(--bg);
    display: flex;
    flex-direction: column;
    align-items: center;
    justify-content: center;
    gap: 44px;
  }
  .card {
    width: 820px;
    height: 468px;
    box-shadow: 0 2px 10px rgba(0,0,0,0.08);
  }
  .card-back {
    background: var(--card-slate);
    display: flex;
    flex-direction: column;
    align-items: center;
    justify-content: center;
    gap: 14px;
  }
  .brand-mark {
    width: 18px; height: 18px;
    border-radius: 50%;
    background: var(--teal);
    margin-bottom: 10px;
  }
  .brand-name, .brand-tagline {
    font-family: "Noto Serif", serif;
    font-weight: 400;
    color: var(--teal);
    text-transform: uppercase;
  }
  .brand-name { font-size: 52px; letter-spacing: 3px; }
  .brand-tagline { font-size: 17px; letter-spacing: 6px; }

  .card-front {
    background: var(--card-white);
    display: flex;
    flex-direction: column;
    align-items: center;
    justify-content: center;
    text-align: center;
  }
  .person-name {
    font-family: "Noto Serif", serif;
    font-weight: 700;
    font-size: 44px;
    color: var(--ink);
  }
  .person-role {
    font-family: "Roboto", sans-serif;
    font-size: 22px;
    color: var(--muted);
    margin-top: 4px;
  }
  .divider {
    width: 56px; height: 2px;
    background: var(--rule);
    margin: 22px 0 20px;
  }
  .contact-list {
    list-style: none;
    font-family: "Roboto", sans-serif;
    font-size: 22px;
    color: var(--muted);
    display: flex;
    flex-direction: column;
    align-items: center;
    gap: 10px;
  }
  .contact-item { display: flex; align-items: center; gap: 10px; }
  .contact-icon { width: 20px; height: 20px; flex: none; }
  .abn-label { color: var(--teal); font-weight: 500; }
</style>
</head>
<body>
  <section class="card card-back" aria-label="Card back">
    <div class="brand-mark"></div>
    <div class="brand-name">Silver Bloom</div>
    <div class="brand-tagline">Marisol's Cleaning Service</div>
  </section>

  <section class="card card-front" aria-label="Card front">
    <h1 class="person-name">Marisol Quenby</h1>
    <p class="person-role">Director</p>
    <div class="divider"></div>
    <ul class="contact-list">
      <li class="contact-item">
        <svg class="contact-icon" viewBox="0 0 24 24" aria-hidden="true"><path fill="#5fbcbb" d="M6.6 10.8a15.1 15.1 0 0 0 6.6 6.6l2.2-2.2c.3-.3.7-.4 1-.2 1.1.4 2.3.6 3.6.6.6 0 1 .4 1 1V20c0 .6-.4 1-1 1C10.6 21 3 13.4 3 4c0-.6.4-1 1-1h3.5c.6 0 1 .4 1 1 0 1.3.2 2.5.6 3.6.1.3 0 .7-.2 1z"/></svg>
        <span>0417906354</span>
      </li>
      <li class="contact-item">
        <svg class="contact-icon" viewBox="0 0 24 24" aria-hidden="true"><rect x="3" y="5.5" width="18" height="13" rx="1" fill="none" stroke="#5fbcbb" stroke-width="1.6"/><path d="M3.5 6.5 12 13l8.5-6.5" fill="none" stroke="#5fbcbb" stroke-width="1.6"/></svg>
        <span>marisolssilvercleaning@tidymail.example</span>
      </li>
      <li class="contact-item">
        <span><span class="abn-label">ABN :</span> 31647209853</span>
      </li>
    </ul>
  </section>
</body>
</html>
```